USB Flash Drive Catalogue

I would like to make a paper catalogue of the products from our Crafterly store. There are currently 209 items on Crafterly. Some would be excluded. The listings have pricing and would need to be organized a bit different but all the information is there.

https://www.crafterly.com/shop/TurboStickHub/items?ref=pagination&page=1

```html
<!DOCTYPE html>
<html lang="en">
<head>
<meta charset="utf-8">
<title>TurboStickHub Catalog 2017 – Pages 10–11</title>
<link href="https://fonts.googleapis.com/css2?family=Ubuntu:wght@400;500;700&display=swap" rel="stylesheet">
<style>
  :root {
    --paper: #ffffff;
    --backdrop: #e4e3df;
    --ink: #2f2f2f;
    --ink-soft: #6d6d6d;
    --accent: #e07b22;
    --band: #3a3a3a;
    --maple-light: #efe9dc;
    --maple-mid: #cdbd9c;
    --walnut-light: #8a6a52;
    --walnut-dark: #4a3424;
    --birch-light: #f1dba8;
    --birch-dark: #c99a55;
  }
  * { box-sizing: border-box; margin: 0; padding: 0; }
  html, body { width: 1200px; height: 804px; overflow: hidden; }
  body {
    background: var(--backdrop);
    font-family: "Ubuntu", sans-serif;
    color: var(--ink);
    display: flex;
  }
  .page {
    position: relative;
    width: 600px;
    height: 804px;
    background: var(--paper);
  }
  .page--left { box-shadow: inset -14px 0 18px -14px rgba(0,0,0,.18); }
  .page--right { box-shadow: inset 14px 0 18px -14px rgba(0,0,0,.18); }

  .brand-band {
    position: absolute;
    top: 30px;
    height: 26px;
    width: 200px;
    background: var(--band);
    display: flex;
    align-items: center;
    gap: 10px;
    padding: 0 16px;
  }
  .page--left .brand-band { left: 0; clip-path: polygon(0 0, 100% 0, 88% 100%, 0 100%); }
  .page--right .brand-band { right: 0; justify-content: flex-end; clip-path: polygon(0 0, 100% 0, 100% 100%, 12% 100%); }
  .brand-dot { width: 10px; height: 10px; border-radius: 50%; background: #d7d7d7; }
  .brand-name { color: #ffffff; font-size: 11px; font-weight: 500; letter-spacing: .3px; }

  .shop-url {
    position: absolute;
    top: 36px;
    font-size: 9px;
    font-weight: 700;
    letter-spacing: .6px;
    color: var(--ink);
  }
  .page--left .shop-url { right: 40px; }
  .page--right .shop-url { left: 40px; }

  .product-grid {
    position: absolute;
    top: 78px;
    left: 40px;
    right: 40px;
    display: grid;
    grid-template-columns: 1fr 1fr;
    grid-template-rows: repeat(3, 222px);
    column-gap: 34px;
  }
  .product { display: flex; flex-direction: column; }
  .product-photo {
    width: 120px;
    height: 96px;
    margin: 4px auto 12px;
    border-radius: 4px;
  }
  .product-photo--maple { background: linear-gradient(150deg, var(--maple-light), var(--maple-mid)); }
  .product-photo--walnut { background: linear-gradient(150deg, var(--walnut-light), var(--walnut-dark)); }
  .product-photo--birch { background: linear-gradient(150deg, var(--birch-light), var(--birch-dark)); }

  .product-head {
    display: flex;
    align-items: flex-end;
    justify-content: space-between;
    border-bottom: 1px solid var(--accent);
    padding-bottom: 3px;
    margin-bottom: 5px;
  }
  .product-title { font-size: 13px; font-weight: 500; color: var(--ink); }
  .price-block { display: flex; flex-direction: column; align-items: flex-end; }
  .capacity { font-size: 11px; font-weight: 500; color: var(--accent); line-height: 1.1; }
  .price {
    background: var(--accent);
    color: #ffffff;
    font-size: 12px;
    font-weight: 500;
    padding: 1px 5px;
    margin-bottom: -4px;
  }
  .specs { list-style: none; font-size: 7px; line-height: 1.35; color: var(--ink); }
  .specs li { margin-bottom: 4px; }
  .specs .dim { display: block; color: var(--ink-soft); padding-left: 10px; }
  .tagline { font-size: 7px; color: var(--ink-soft); margin-bottom: 8px; }

  .contact {
    position: absolute;
    bottom: 56px;
    font-size: 8px;
    color: var(--ink-soft);
    letter-spacing: .3px;
  }
  .page--left .contact { right: 40px; }
  .page--right .contact { left: 40px; }
  .folio {
    position: absolute;
    bottom: 26px;
    font-size: 8px;
    color: var(--ink-soft);
    letter-spacing: .4px;
  }
  .folio strong { color: var(--accent); font-weight: 500; }
  .page--left .folio { left: 40px; }
  .page--right .folio { right: 40px; }
</style>
</head>
<body>

<section class="page page--left">
  <div class="brand-band"><span class="brand-dot"></span><span class="brand-name">TurboStickHub</span></div>
  <div class="shop-url">www.crafterly.com/shop/TurboStickHub</div>

  <div class="product-grid">
    <article class="product">
      <div class="product-photo product-photo--maple" role="img" aria-label="White maple box engraved Just Married with wooden USB drive on raffia"></div>
      <div class="product-head"><h3 class="product-title">Antique Maple Wood</h3><div class="price-block"><span class="capacity">16 GB</span><span class="price">$ 25.95</span></div></div>
      <ul class="specs">
        <li>(1) Laser Engraved Maple wooden box filled Raffia grass.<span class="dim">Approximate dimensions: 104 x 96 x 39mm</span></li>
        <li>(1) 16GB maple wood USB drive, Wildwood Body, painted in Wedding White.<span class="dim">Approximate dimensions: 60 x 28 x 10mm</span></li>
      </ul>
    </article>
    <article class="product">
      <div class="product-photo product-photo--maple" role="img" aria-label="White maple box engraved Sweet 16 with heart USB drive on raffia"></div>
      <div class="product-head"><h3 class="product-title">Antique Maple Wood</h3><div class="price-block"><span class="capacity">16 GB</span><span class="price">$ 21.95</span></div></div>
      <ul class="specs">
        <li>(1) Laser Engraved Maple wooden box filled Raffia grass.<span class="dim">Approximate dimensions: 104 x 96 x 39mm</span></li>
        <li>(1) maple wood USB drive, painted in Wedding White.<span class="dim">Approximate dimensions: 60 x 28 x 10mm</span></li>
      </ul>
    </article>
    <article class="product">
      <div class="product-photo product-photo--walnut" role="img" aria-label="Walnut box engraved Mazel Tov with walnut USB drive"></div>
      <div class="product-head"><h3 class="product-title">Walnut Wood Flash Drive</h3><div class="price-block"><span class="capacity">8GB/16GB</span><span class="price">$ 22.95</span></div></div>
      <ul class="specs">
        <li>(1) Laser Engraved Walnut wooden box filled Raffia grass.<span class="dim">Approximate dimensions: 104 x 96 x 39mm</span></li>
        <li>(1) Walnut wood USB drive<span class="dim">Approximate dimensions: 60 x 28 x 10mm</span></li>
      </ul>
    </article>
    <article class="product">
      <div class="product-photo product-photo--birch" role="img" aria-label="Natural maple photo box engraved Just Married"></div>
      <div class="product-head"><h3 class="product-title">Wooden Photo Box</h3><div class="price-block"><span class="capacity">4x6</span><span class="price">$ 22.95</span></div></div>
      <p class="tagline">Great for artisans, enthusiasts, and gift givers!</p>
      <ul class="specs"><li>Over all dimensions:<span class="dim">180x130x60mm</span></li></ul>
    </article>
    <article class="product">
      <div class="product-photo product-photo--maple" role="img" aria-label="White maple box engraved Just Married with wooden USB drive on raffia"></div>
      <div class="product-head"><h3 class="product-title">Antique Maple Wood</h3><div class="price-block"><span class="capacity">16 GB</span><span class="price">$ 25.95</span></div></div>
      <ul class="specs">
        <li>(1) Laser Engraved Maple wooden box filled Raffia grass.<span class="dim">Approximate dimensions: 104 x 96 x 39mm</span></li>
        <li>(1) 16GB maple wood USB drive, Wildwood Body, painted in Wedding White.<span class="dim">Approximate dimensions: 60 x 28 x 10mm</span></li>
      </ul>
    </article>
    <article class="product">
      <div class="product-photo product-photo--maple" role="img" aria-label="White maple box engraved Sweet 16 with heart USB drive on raffia"></div>
      <div class="product-head"><h3 class="product-title">Antique Maple Wood</h3><div class="price-block"><span class="capacity">16 GB</span><span class="price">$ 21.95</span></div></div>
      <ul class="specs">
        <li>(1) Laser Engraved Maple wooden box filled Raffia grass.<span class="dim">Approximate dimensions: 104 x 96 x 39mm</span></li>
        <li>(1) maple wood USB drive, painted in Wedding White.<span class="dim">Approximate dimensions: 60 x 28 x 10mm</span></li>
      </ul>
    </article>
  </div>

  <p class="contact">Phone: 800-555-0147 | hello@turbostickhub.com</p>
  <p class="folio"><strong>PAGE 10</strong> | Catalog 2017</p>
</section>

<section class="page page--right">
  <div class="brand-band"><span class="brand-name">TurboStickHub</span><span class="brand-dot"></span></div>
  <div class="shop-url">www.crafterly.com/shop/TurboStickHub</div>

  <div class="product-grid">
    <article class="product">
      <div class="product-photo product-photo--maple" role="img" aria-label="White maple box engraved Just Married with wooden USB drive on raffia"></div>
      <div class="product-head"><h3 class="product-title">Antique Maple Wood</h3><div class="price-block"><span class="capacity">16 GB</span><span class="price">$ 25.95</span></div></div>
      <ul class="specs">
        <li>(1) Laser Engraved Maple wooden box filled Raffia grass.<span class="dim">Approximate dimensions: 104 x 96 x 39mm</span></li>
        <li>(1) 16GB maple wood USB drive, Wildwood Body, painted in Wedding White.<span class="dim">Approximate dimensions: 60 x 28 x 10mm</span></li>
      </ul>
    </article>
    <article class="product">
      <div class="product-photo product-photo--maple" role="img" aria-label="White maple box engraved Sweet 16 with heart USB drive on raffia"></div>
      <div class="product-head"><h3 class="product-title">Antique Maple Wood</h3><div class="price-block"><span class="capacity">16 GB</span><span class="price">$ 21.95</span></div></div>
      <ul class="specs">
        <li>(1) Laser Engraved Maple wooden box filled Raffia grass.<span class="dim">Approximate dimensions: 104 x 96 x 39mm</span></li>
        <li>(1) maple wood USB drive, painted in Wedding White.<span class="dim">Approximate dimensions: 60 x 28 x 10mm</span></li>
      </ul>
    </article>
    <article class="product">
      <div class="product-photo product-photo--walnut" role="img" aria-label="Walnut box engraved Mazel Tov with walnut USB drive"></div>
      <div class="product-head"><h3 class="product-title">Walnut Wood Flash Drive</h3><div class="price-block"><span class="capacity">8GB/16GB</span><span class="price">$ 22.95</span></div></div>
      <ul class="specs">
        <li>(1) Laser Engraved Walnut wooden box filled Raffia grass.<span class="dim">Approximate dimensions: 104 x 96 x 39mm</span></li>
        <li>(1) Walnut wood USB drive<span class="dim">Approximate dimensions: 60 x 28 x 10mm</span></li>
      </ul>
    </article>
    <article class="product">
      <div class="product-photo product-photo--birch" role="img" aria-label="Natural maple photo box engraved Just Married"></div>
      <div class="product-head"><h3 class="product-title">Wooden Photo Box</h3><div class="price-block"><span class="capacity">4x6</span><span class="price">$ 22.95</span></div></div>
      <p class="tagline">Great for artisans, enthusiasts, and gift givers!</p>
      <ul class="specs"><li>Over all dimensions:<span class="dim">180x130x60mm</span></li></ul>
    </article>
    <article class="product">
      <div class="product-photo product-photo--maple" role="img" aria-label="White maple box engraved Just Married with wooden USB drive on raffia"></div>
      <div class="product-head"><h3 class="product-title">Antique Maple Wood</h3><div class="price-block"><span class="capacity">16 GB</span><span class="price">$ 25.95</span></div></div>
      <ul class="specs">
        <li>(1) Laser Engraved Maple wooden box filled Raffia grass.<span class="dim">Approximate dimensions: 104 x 96 x 39mm</span></li>
        <li>(1) 16GB maple wood USB drive, Wildwood Body, painted in Wedding White.<span class="dim">Approximate dimensions: 60 x 28 x 10mm</span></li>
      </ul>
    </article>
    <article class="product">
      <div class="product-photo product-photo--maple" role="img" aria-label="White maple box engraved Sweet 16 with heart USB drive on raffia"></div>
      <div class="product-head"><h3 class="product-title">Antique Maple Wood</h3><div class="price-block"><span class="capacity">16 GB</span><span class="price">$ 21.95</span></div></div>
      <ul class="specs">
        <li>(1) Laser Engraved Maple wooden box filled Raffia grass.<span class="dim">Approximate dimensions: 104 x 96 x 39mm</span></li>
        <li>(1) maple wood USB drive, painted in Wedding White.<span class="dim">Approximate dimensions: 60 x 28 x 10mm</span></li>
      </ul>
    </article>
  </div>

  <p class="contact">Phone: 800-555-0147 | hello@turbostickhub.com</p>
  <p class="folio">Catalog 2017 | <strong>PAGE 11</strong></p>
</section>

</body>
</html>
```